Good afternoon,
1. Can we also have the ‘Marblewren selections of the month’ moved to the left side and smaller than the logo quote ‘bright hearts at daybreak’ as it’s just a subheading. That said can we have the ‘Bright hearts at daybreak’ a little larger.
2. Can we have the order of the drop down menus as. Age then Theme then Location (no price). Next to these titles can we have a small image such as a locator point next to ‘location’, two people holding hands adult and child net to ‘age’ and something adventure/city next to ‘theme’, an image to represent the drop down menus. See below:

3. Can we please use this as a logo instead of what we have at the moment. And the same type of setup as what I have here. I really like this map of Australia. We have the rights to it and I have attached it as a file for you to use.

4. Can the selection buttons all be the same blue as the blue in the logo please. Can every part of the page have the logo blue/dirty orange also? Makes it calmer.

5. Could you please add a ‘calendar’ to the tabs (in blue at the top of the page, on the left of ‘add and activity’ .
Let me know how you go. Thanks

Target Market(s)

• Parents and care-givers
• Teachers
• Children (child-friendly)
• Customers are those who ask the question ‘what am I going to do with my child/ren this week/weekend/month’

Industry/Entity Type

Quote

Number of Pages Required

4 page

Font styles to use
Sans Serif

Requirements
Must have
• An ecommerce website (platform) with a responsive system for IOS and Android
• Easy to navigate, user-friendly clean
Nice to have
• some interactive maps
Should not have
• To much clutter/info

```html
<!DOCTYPE html>
<html lang="en">
<head>
<meta charset="utf-8">
<title>Marblewren Melbourne</title>
<link rel="stylesheet" href="https://fonts.googleapis.com/css2?family=Hind:wght@400;500;600&family=Open+Sans:wght@400;600;700&family=Khand:wght@600&display=swap">
<style>
:root{
  --blue:#2f7fb8;
  --blue-deep:#25689a;
  --orange:#d9824a;
  --orange-deep:#cf7641;
  --ink:#1b1b1b;
  --panel:#ececec;
  --white:#ffffff;
  --grey-text:#555555;
  --footer:#2b2b2b;
  --footer-bar:#141414;
  --line:#cfcfcf;
}
*{box-sizing:border-box;margin:0;padding:0}
html,body{width:1200px;height:2281px;overflow:hidden}
body{position:relative;background:var(--white);font-family:"Open Sans",Arial,sans-serif;color:var(--ink)}
.abs{position:absolute}

/* header */
.brand{left:61px;top:20px;display:flex;align-items:center;gap:14px}
.brand-mark{width:66px;height:66px;border-radius:6px;background:linear-gradient(135deg,#e9a36e,var(--orange))}
.brand-text{display:flex;flex-direction:column}
.brand-name{font-family:"Hind",Arial,sans-serif;font-weight:600;font-size:40px;line-height:40px;color:var(--blue)}
.brand-quote{font-family:"Hind",Arial,sans-serif;font-size:22px;line-height:26px;color:var(--orange);margin-top:4px}
.top-btn{top:35px;height:43px;background:var(--blue);color:var(--white);font-family:"Hind",Arial,sans-serif;font-size:16px;display:flex;align-items:center;justify-content:center;border-radius:2px}
.top-btn.suggest{left:827px;width:160px}
.top-btn.login{left:999px;width:142px}

.main-nav{left:0;top:108px;width:1200px;height:43px;background:var(--ink)}
.main-nav ul{list-style:none;display:flex;height:100%;padding-left:61px}
.main-nav li{font-weight:700;font-size:14px;color:var(--white);display:flex;align-items:center;padding:0 11px;margin-right:18px}
.main-nav li.active{background:var(--orange)}
.main-nav li.calendar{background:var(--blue)}
.search-icon{right:56px;top:116px}

/* finder panel */
.finder{left:61px;top:210px;width:331px;height:417px;background:var(--panel)}
.finder-head{height:87px;background:var(--orange);color:var(--white);font-family:"Hind",Arial,sans-serif;font-size:25px;line-height:29px;padding:14px 20px}
.field{position:absolute;left:32px;width:261px;height:44px;background:var(--white);border:1px solid var(--line);border-radius:2px;display:flex;align-items:center;padding-left:44px;font-size:14px;color:#666}
.field svg.ico{position:absolute;left:12px;top:11px}
.field .caret{position:absolute;right:14px;top:18px}
.field.age{top:128px}.field.theme{top:185px}.field.place{top:242px}
.finder-btn{position:absolute;left:32px;top:319px;width:259px;height:54px;background:var(--blue);color:var(--white);font-family:"Hind",Arial,sans-serif;font-size:20px;display:flex;align-items:center;justify-content:center;border-radius:3px}

/* themes */
.themes{left:450px;top:210px;width:691px;height:681px;background:var(--panel)}
.themes-head{height:60px;background:var(--orange);display:flex;align-items:center;padding-left:15px;color:var(--white);font-family:"Hind",Arial,sans-serif;font-size:25px}
.theme-select{position:absolute;left:247px;top:13px;width:235px;height:36px;background:var(--white);border-radius:2px;font-size:14px;color:#888;padding:8px 14px}
.theme-select .caret{position:absolute;right:10px;top:15px}
.arrows{position:absolute;display:flex;gap:4px}
.arrows span{width:37px;height:33px;background:var(--blue-deep);display:flex;align-items:center;justify-content:center}
.themes .arrows{left:597px;top:14px}
.tile-photo{position:absolute;width:189px;height:180px;border:3px solid var(--white);box-shadow:0 0 2px rgba(0,0,0,.25)}
.tile-btn{position:absolute;width:197px;height:48px;background:var(--blue);color:var(--white);font-family:"Hind",Arial,sans-serif;font-weight:600;font-size:19px;display:flex;align-items:center;justify-content:center;border-radius:2px}
.tile-btn::before{content:"";position:absolute;left:16px;top:-10px;border-left:10px solid transparent;border-right:10px solid transparent;border-bottom:10px solid var(--blue)}
.gallery{background:linear-gradient(135deg,#6b4a2a,#c99a5a 60%,#3a2a1c)}
.forest{background:linear-gradient(160deg,#4b5a3a,#7c8a5c 50%,#3b3326)}
.tower{background:linear-gradient(180deg,#6f9bd0,#2c3a58 70%,#1c2230)}
.wall{background:linear-gradient(140deg,#7a2a3a,#3a4a7a 50%,#a43a3a)}

/* selections */
.band{left:0;top:1025px;width:1200px;height:58px;background:var(--orange-deep);color:var(--white);font-family:"Hind",Arial,sans-serif;font-size:20px;line-height:58px;padding:0 61px}
.band .arrows{left:1063px;top:12px}
.band-body{left:0;top:1083px;width:1200px;height:554px;background:var(--panel)}
.card{position:absolute;top:1138px;width:327px;height:426px;background:var(--white);border:1px solid #e0e0e0}
.card-photo{height:222px}
.card h3{font-family:"Hind",Arial,sans-serif;font-weight:600;font-size:19px;line-height:22px;padding:0 20px;margin-top:24px;color:#111}
.card p{font-size:13px;line-height:21px;color:var(--grey-text);padding:0 20px;margin-top:10px}
.card.mid h3,.card.right h3{margin-top:34px}
.run{background:linear-gradient(160deg,#9cc0d8,#7f9a5a 45%,#c0a278)}
.ship{background:linear-gradient(180deg,#e9ddc5,#b8955e 70%,#7a3a2a)}
.craft{background:linear-gradient(150deg,#f1ece6,#e48aa8 55%,#c9b08a)}

/* newsletter */
.news-title{left:0;top:1696px;width:1200px;text-align:center;font-family:"Khand",Arial,sans-serif;font-weight:600;font-size:44px;line-height:52px;color:#161616}
.news-sub{left:0;top:1756px;width:1200px;text-align:center;font-size:14px;color:#222}
.news-input{left:377px;top:1813px;width:374px;height:38px;border:1px solid #999;font-size:14px;color:#888;padding:9px 12px}
.news-submit{left:750px;top:1813px;width:106px;height:38px;background:var(--blue);color:var(--white);font-weight:700;font-size:16px;display:flex;align-items:center;justify-content:center}

/* footer */
.footer{left:0;top:1921px;width:1200px;height:318px;background:var(--footer);color:var(--white)}
.foot-col{position:absolute;top:49px}
.foot-col h4{font-family:"Hind",Arial,sans-serif;font-weight:500;font-size:25px;line-height:30px}
.foot-col h4::after{content:"";display:block;width:54px;height:3px;background:var(--orange);margin-top:8px}
.contact-line{display:flex;align-items:center;gap:12px;font-size:13px;margin-top:14px}
.contact-line:first-of-type{margin-top:26px}
.socials{display:flex;gap:7px;margin-top:24px}
.socials span{width:29px;height:29px;border-radius:50%;background:var(--blue)}
.foot-col ul{list-style:none;margin-top:22px}
.foot-col li{font-size:13px;line-height:23px}
.services li::before{content:"";display:inline-block;width:6px;height:6px;border-radius:50%;background:var(--orange);margin:0 10px 2px 6px}
.hours li{line-height:26px}
.map{position:absolute;left:0;top:75px;width:254px;height:165px;background:linear-gradient(135deg,#e8e2d2,#f1d9a6 50%,#cfdcc2);border:2px solid var(--white)}
.copyright{left:0;top:2239px;width:1200px;height:42px;background:var(--footer-bar);color:#ddd;font-size:13px;display:flex;align-items:center;justify-content:center}
</style>
</head>
<body>

<div class="abs brand">
  <span class="brand-mark" role="img" aria-label="Map of Australia"></span>
  <div class="brand-text">
    <span class="brand-name">Marblewren</span>
    <span class="brand-quote">Bright hearts at daybreak</span>
  </div>
</div>
<div class="abs top-btn suggest">See our Suggestion</div>
<div class="abs top-btn login">Signup/Login</div>

<nav class="abs main-nav">
  <ul>
    <li class="active">HOME</li>
    <li>FEATURED ADVENTURES</li>
    <li class="calendar">CALENDAR</li>
    <li>LIST AN ACTIVITY</li>
    <li>DESTINATION</li>
  </ul>
</nav>
<svg class="abs search-icon" width="26" height="26" viewBox="0 0 26 26"><circle cx="10.5" cy="10.5" r="7.5" fill="none" stroke="#fff" stroke-width="3"/><line x1="16" y1="16" x2="23" y2="23" stroke="#fff" stroke-width="3.5" stroke-linecap="round"/></svg>

<section class="abs finder">
  <div class="finder-head">What to do with your children in Paris?</div>
  <div class="field age">
    <svg class="ico" width="24" height="22" viewBox="0 0 24 22"><circle cx="6" cy="3.5" r="3" fill="#2f7fb8"/><path d="M2 9h8v7H8v6H4v-6H2z" fill="#2f7fb8"/><circle cx="18" cy="8" r="2.4" fill="#2f7fb8"/><path d="M15 12h6v5h-1.5v5h-3v-5H15z" fill="#2f7fb8"/><path d="M10 11h5" stroke="#2f7fb8" stroke-width="1.6"/></svg>
    Age
    <svg class="caret" width="14" height="8" viewBox="0 0 14 8"><path d="M0 0h14L7 8z" fill="#888"/></svg>
  </div>
  <div class="field theme">
    <svg class="ico" width="24" height="22" viewBox="0 0 24 22"><rect x="1" y="8" width="6" height="14" fill="#2f7fb8"/><rect x="8" y="2" width="7" height="20" fill="#2f7fb8"/><rect x="16" y="11" width="7" height="11" fill="#2f7fb8"/><path d="M10 5h3M10 9h3M10 13h3" stroke="#fff" stroke-width="1.4"/></svg>
    Theme
    <svg class="caret" width="14" height="8" viewBox="0 0 14 8"><path d="M0 0h14L7 8z" fill="#888"/></svg>
  </div>
  <div class="field place">
    <svg class="ico" width="24" height="22" viewBox="0 0 24 22"><path d="M12 0a7 7 0 0 1 7 7c0 5-7 15-7 15S5 12 5 7a7 7 0 0 1 7-7z" fill="#2f7fb8"/><circle cx="12" cy="7" r="2.6" fill="#fff"/></svg>
    Location
    <svg class="caret" width="14" height="8" viewBox="0 0 14 8"><path d="M0 0h14L7 8z" fill="#888"/></svg>
  </div>
  <div class="finder-btn">See your suggestion</div>
</section>

<section class="abs themes">
  <div class="themes-head">Explore by Theme</div>
  <div class="theme-select">Art<svg class="caret" width="14" height="8" viewBox="0 0 14 8"><path d="M0 0h14L7 8z" fill="#999"/></svg></div>
  <div class="arrows">
    <span><svg width="18" height="14" viewBox="0 0 18 14"><path d="M17 7H2M7 1 1 7l6 6" fill="none" stroke="#fff" stroke-width="2.5"/></svg></span>
    <span><svg width="18" height="14" viewBox="0 0 18 14"><path d="M1 7h15M11 1l6 6-6 6" fill="none" stroke="#fff" stroke-width="2.5"/></svg></span>
  </div>

  <div class="tile-photo gallery" style="left:26px;top:91px" role="img" aria-label="Child walking through a gallery of framed paintings"></div>
  <div class="tile-photo forest" style="left:251px;top:91px" role="img" aria-label="Fern forest with a fallen tree trunk"></div>
  <div class="tile-photo forest" style="left:476px;top:91px" role="img" aria-label="Fern forest with a fallen tree trunk"></div>
  <div class="tile-btn" style="left:25px;top:301px">Explore History</div>
  <div class="tile-btn" style="left:250px;top:301px">Explore History</div>
  <div class="tile-btn" style="left:474px;top:299px">Explore History</div>

  <div class="tile-photo tower" style="left:32px;top:385px" role="img" aria-label="Child looking up at a tall spire against blue sky"></div>
  <div class="tile-photo wall" style="left:257px;top:385px" role="img" aria-label="Visitor touching a colourful wall of book covers"></div>
  <div class="tile-photo forest" style="left:482px;top:385px" role="img" aria-label="Fern forest with a fallen tree trunk"></div>
  <div class="tile-btn" style="left:31px;top:595px">Explore History</div>
  <div class="tile-btn" style="left:256px;top:595px">Explore History</div>
  <div class="tile-btn" style="left:481px;top:593px">Explore History</div>
</section>

<div class="abs band">Marblewren selections of the month
  <div class="arrows">
    <span><svg width="18" height="14" viewBox="0 0 18 14"><path d="M17 7H2M7 1 1 7l6 6" fill="none" stroke="#fff" stroke-width="2.5"/></svg></span>
    <span><svg width="18" height="14" viewBox="0 0 18 14"><path d="M1 7h15M11 1l6 6-6 6" fill="none" stroke="#fff" stroke-width="2.5"/></svg></span>
  </div>
</div>
<div class="abs band-body"></div>

<article class="card" style="left:61px">
  <div class="card-photo run" role="img" aria-label="Two children running a trail race in the mountains"></div>
  <h3>Concert of classical music and stories told</h3>
  <p>Lorem Ipsum has been the industry's standard dummy text ever since the 1500s, when an unknown printer took a galley of type and scrambled it to make a type specimen book.</p>
</article>
<article class="card mid" style="left:441px">
  <div class="card-photo ship" role="img" aria-label="Child holding a ship wheel on top of old suitcases"></div>
  <h3>Concert of classical music and stories told</h3>
  <p>Lorem Ipsum has been the industry's standard dummy text ever since the 1500s, when an unknown printer took a galley of type and scrambled it to make a type specimen book.</p>
</article>
<article class="card right" style="left:812px">
  <div class="card-photo craft" role="img" aria-label="Children making colourful craft puppets"></div>
  <h3>Concert of classical music and stories told</h3>
  <p>Lorem Ipsum has been the industry's standard dummy text ever since the 1500s, when an unknown printer took a galley of type and scrambled it to make a type specimen book.</p>
</article>

<h2 class="abs news-title">Get Started With Our Newsletter</h2>
<p class="abs news-sub">Free shipping, phenomenal customer service and wicked prices.</p>
<div class="abs news-input">Enter your Email here</div>
<div class="abs news-submit">Submit</div>

<footer class="abs footer">
  <div class="foot-col" style="left:61px">
    <h4>Contact us</h4>
    <div class="contact-line"><svg width="16" height="16" viewBox="0 0 16 16"><path d="M3 0l3 4-2 2c1 2 4 5 6 6l2-2 4 3-2 3C7 16 0 9 0 3z" fill="#fff"/></svg>9384150227</div>
    <div class="contact-line"><svg width="18" height="13" viewBox="0 0 18 13"><rect x="0.5" y="0.5" width="17" height="12" fill="none" stroke="#fff"/><path d="M1 1l8 6 8-6" fill="none" stroke="#fff"/></svg>contact@marblewren.com.au</div>
    <div class="socials"><span></span><span></span><span></span><span></span></div>
  </div>
  <div class="foot-col services" style="left:376px">
    <h4>Our Services</h4>
    <ul><li>Home</li><li>About Us</li><li>News</li><li>Free Tests</li><li>Kestrel Stores</li><li>Community</li><li>Courses</li></ul>
  </div>
  <div class="foot-col hours" style="left:628px">
    <h4>Store Hours</h4>
    <ul><li>Monday:10am - 8pm</li><li>Tuesday:10am - 7pm</li><li>Wednesday:10am - 8pm</li><li>Thrusday: 10am - 8pm</li><li>Friday:10am - 8pm</li><li>Saturday:10am - 7pm</li></ul>
  </div>
  <div class="foot-col" style="left:870px">
    <h4>Our Location</h4>
    <div class="map" role="img" aria-label="Street map showing the store location"></div>
  </div>
</footer>
<div class="abs copyright">© 2016 Copyright Marblewren. All Right Reserved</div>

</body>
</html>
```